Powepoint Templates From Logo

We need 3 Powerpoint templates for use in a variety of presentations we develop and customize. Primary uses of the powerpoint presentations are for printed "pitch books" describing our firm's capabilities and approach (a lot of words with some design elements that we have developed), printed presentations of the results of financial evaluations of our clients (lots of charts and graphs) and as the talking points for speeches.

The design needs to be professional and "solid" to establish that we are capable of selling your multi-million dollar business, but also be a little different to show that we are not just boring MBA's.

Our current website and other materials have been developed internally and leave a great deal to be desired. I have initiated this project to demonstrate how much our look can be improved and, if successful, I hope to do much bigger projects in the future.
Updates

This is my first project and I thaank you all for your participation. Since I am new to this, I don;t know if I am providing the help and feedback as I should. Please feel free to let me know how I can be a better customer.

Target Market(s)

professionals (lawyers, accountaants), business owners, business groups, technology people

Industry/Entity Type

Financial

Requirements
Must have
• our logo
a place where logo of client can be inserted if appropriate
templates for the following pages
title page
standard bullet narrative page
page for charts and graphs to mostly fill the page
Should not have a lot of dark solid color that has to be printed.

Nice to have
• something to perk up the color a little

```html
<!DOCTYPE html>
<html lang="en">
<head>
<meta charset="utf-8">
<title>Title Slide</title>
<link rel="stylesheet" href="https://fonts.googleapis.com/css2?family=Oswald:wght@700&family=Arimo:wght@400;700&display=swap">
<style>
  :root {
    --navy-deep: #143d72;
    --navy-mid: #6f93bd;
    --sky-light: #cbdaeb;
    --floor-top: #eaf2fb;
    --floor-bottom: #f6f9fe;
    --title-navy: #12386c;
    --brand-navy: #173f72;
    --subtitle-grey: #3b3d40;
    --photo-a: #9aa5a8;
    --photo-b: #3a3c44;
  }
  html, body {
    margin: 0;
    padding: 0;
    overflow: hidden;
    background: #ffffff;
  }
  .slide {
    position: relative;
    width: 1200px;
    height: 900px;
    overflow: hidden;
    background: linear-gradient(180deg, var(--floor-top) 0%, var(--floor-bottom) 100%);
    font-family: "Arimo", Arial, sans-serif;
  }
  .sky-band {
    position: absolute;
    left: 0;
    top: 0;
    width: 1200px;
    height: 470px;
    background: linear-gradient(180deg, var(--navy-deep) 0%, var(--navy-mid) 45%, var(--sky-light) 100%);
  }
  .portrait {
    position: absolute;
    left: 228px;
    top: 240px;
    width: 182px;
    height: 236px;
    border-radius: 26px;
    background: linear-gradient(160deg, var(--photo-a) 0%, #6b7276 45%, var(--photo-b) 100%);
  }
  .project-title {
    position: absolute;
    right: 33px;
    top: 396px;
    margin: 0;
    font-family: "Oswald", "Arial Narrow", sans-serif;
    font-weight: 700;
    font-size: 74px;
    line-height: 1;
    letter-spacing: 0.5px;
    color: var(--title-navy);
    text-transform: uppercase;
  }
  .subtitle {
    position: absolute;
    left: 102px;
    top: 798px;
    margin: 0;
    font-size: 40px;
    font-weight: 400;
    letter-spacing: -0.5px;
    color: var(--subtitle-grey);
  }
  .brand {
    position: absolute;
    right: 33px;
    top: 768px;
    text-align: right;
    color: var(--brand-navy);
  }
  .brand-name {
    display: flex;
    align-items: center;
    justify-content: flex-end;
    gap: 14px;
    font-size: 50px;
    font-weight: 700;
    line-height: 1;
    letter-spacing: 1px;
  }
  .brand-square {
    width: 30px;
    height: 30px;
    background: var(--brand-navy);
  }
  .brand-tagline {
    margin-top: 10px;
    font-size: 17px;
    font-weight: 400;
    letter-spacing: 0.6px;
  }
</style>
</head>
<body>
  <main class="slide">
    <div class="sky-band"></div>
    <div class="portrait" role="img" aria-label="Portrait photo of the presenter"></div>
    <h1 class="project-title">Project Title Here</h1>
    <p class="subtitle">Sub title here</p>
    <div class="brand">
      <div class="brand-name"><span class="brand-square"></span>MERIDIAN HALL</div>
      <div class="brand-tagline">MERGERS • ACQUISITIONS • SELL SIDE ADVISORS</div>
    </div>
  </main>
</body>
</html>
```